Meridale Nutrition needs Stationary and a business card

We would like to use our current logo. The text can be moved around as needed. The stationary needs to be a 'first page' where the logo is more prominent to be impressive on higher quality paper and a second page where the logo is more subtle where there will be much more information on the page. There are 2 clinic locations which will need include name, address, phone number, fax number, web address. The business card should be single sided and contain this information also.
The design must be contemporary and sophisticated as this is a science based diet run out of a medical clinic.

Target Market(s)

People wanting to lose weight, athletes looking to optimise performance, people with arthritis or fighting cancer

Industry/Entity Type

Business

Contact Information for Business Card

must use the logo. I have attached an example card with the practice details on it. there must be space for the doctors name. Also the website www.meridalenutrition.com.au

Requirements
Must have
• the logo, the business adresses and phone numbers, the website, the doctors name and qualifications
Nice to have
• some creativity
Should not have
• Do not simply reproduce the existing card please

```html
<!DOCTYPE html>
<html lang="en">
<head>
<meta charset="utf-8">
<title>Meridale Nutrition – Stationery</title>
<link rel="stylesheet" href="https://fonts.googleapis.com/css2?family=Questrial&display=swap">
<style>
  :root {
    --backdrop: #e6e8eb;
    --paper: #ffffff;
    --card-stock: #f4f3ef;
    --navy: #1f4a7a;
    --sky: #2aa8e0;
    --ink: #3d4a5a;
    --muted: #7c8896;
    --rule: #c9d6e2;
    --watermark: #eef1f5;
  }
  * { box-sizing: border-box; margin: 0; padding: 0; }
  html, body {
    width: 1200px; height: 522px; overflow: hidden;
    background: var(--backdrop);
    font-family: "Questrial", sans-serif;
    color: var(--ink);
  }
  .stage { position: relative; width: 1200px; height: 522px; }

  /* Business card */
  .business-card {
    position: absolute; left: 190px; top: 52px;
    width: 180px; height: 258px;
    background: var(--card-stock);
    box-shadow: 0 2px 6px rgba(0,0,0,.12);
    padding: 14px 12px 10px;
    text-align: center;
    font-size: 6.4px; line-height: 1.35;
  }
  .brand-mark { display: flex; flex-direction: column; align-items: center; color: var(--navy); }
  .brand-mark .dot { border-radius: 50%; background: var(--sky); }
  .business-card .brand-mark .dot { width: 22px; height: 22px; margin-bottom: 3px; }
  .business-card .brand-mark .name { font-size: 9px; letter-spacing: .5px; }
  .doctor { color: var(--navy); font-size: 10px; margin-top: 9px; }
  .quals { color: var(--muted); }
  .clinic { margin-top: 6px; padding-top: 5px; border-top: 0.5px solid var(--rule); }
  .clinic-name { color: var(--navy); font-size: 9px; }
  .label { color: var(--navy); }
  .web { color: var(--sky); }

  /* Cover page */
  .cover-page {
    position: absolute; left: 478px; top: 28px;
    width: 326px; height: 466px;
    background: var(--paper);
    box-shadow: 0 2px 8px rgba(0,0,0,.10);
  }
  .cover-page .brand-mark { position: absolute; left: 0; right: 0; top: 140px; }
  .cover-page .brand-mark .dot { width: 150px; height: 150px; margin-bottom: 18px; }
  .cover-page .brand-mark .name { font-size: 29px; letter-spacing: 1px; }

  /* Letterhead */
  .letterhead {
    position: absolute; left: 845px; top: 28px;
    width: 323px; height: 466px;
    background: var(--paper);
    box-shadow: 0 2px 8px rgba(0,0,0,.10);
    overflow: hidden;
  }
  .letterhead .watermark {
    position: absolute; left: 110px; top: 110px;
    width: 230px; height: 300px; border-radius: 50%;
    background: var(--watermark);
  }
  .letterhead .brand-mark { position: absolute; right: 14px; top: 14px; width: 70px; }
  .letterhead .brand-mark .dot { width: 22px; height: 22px; margin-bottom: 2px; }
  .letterhead .brand-mark .name { font-size: 6px; white-space: nowrap; }
  .letterhead .details {
    position: absolute; right: 14px; top: 76px; width: 100px;
    text-align: right; font-size: 4.6px; line-height: 1.45;
  }
  .letterhead .doctor { font-size: 6.5px; margin-top: 0; }
  .letterhead .clinic { border-top: none; padding-top: 0; margin-top: 8px; }
  .letterhead .clinic-name { font-size: 6px; }
</style>
</head>
<body>
<main class="stage">

  <section class="business-card">
    <div class="brand-mark"><span class="dot"></span><span class="name">MERIDALE NUTRITION</span></div>
    <p class="doctor">Dr Lena Varga</p>
    <p class="quals">BMedSc MBBS PhD (Nutrition)<br>Clinical Nutrition Physician</p>
    <div class="clinic">
      <p class="clinic-name">Harbourside</p>
      <p class="label">Address</p>
      <p>14 Wattle Street<br>Harbourside NSW 2999</p>
      <p class="label">Telephone</p>
      <p>(02) 9000 1234</p>
      <p class="label">Weight Management</p>
      <p class="web">www.meridalenutrition.com.au</p>
    </div>
    <div class="clinic">
      <p class="clinic-name">Eastfield</p>
      <p class="label">Address</p>
      <p>8 Ferndale Road<br>Eastfield NSW 2988</p>
      <p class="label">Telephone</p>
      <p>(02) 9000 5678</p>
      <p class="label">Sports Performance</p>
    </div>
  </section>

  <section class="cover-page">
    <div class="brand-mark"><span class="dot"></span><span class="name">MERIDALE NUTRITION</span></div>
  </section>

  <section class="letterhead">
    <div class="watermark"></div>
    <div class="brand-mark"><span class="dot"></span><span class="name">MERIDALE NUTRITION</span></div>
    <div class="details">
      <p class="doctor">Dr Lena Varga</p>
      <p class="quals">BMedSc MBBS PhD (Nutrition)<br>Clinical Nutrition Physician</p>
      <div class="clinic">
        <p class="clinic-name">Harbourside</p>
        <p class="label">Address</p>
        <p>14 Wattle Street<br>Harbourside NSW 2999</p>
        <p class="label">Telephone</p>
        <p>(02) 9000 1234</p>
        <p class="label">Weight Management</p>
      </div>
      <div class="clinic">
        <p class="clinic-name">Eastfield</p>
        <p class="label">Address</p>
        <p>8 Ferndale Road<br>Eastfield NSW 2988</p>
        <p class="label">Telephone</p>
        <p>(02) 9000 5678</p>
        <p class="label">Sports Performance</p>
      </div>
    </div>
  </section>

</main>
</body>
</html>
```